I am looking for a flyer design for my upcoming symposium. Here are the details for the flyer and pictures of speakers are attached.

Name of Symposium: Layered and Regional Proteomics Colloquium, Sponsored by the Dorwick Chromatin Institute and the Department of Bioengineering
Date: January 8, 2018
Location: Halvorsen Auditorium, Brantley Center for Applied Discovery, 2175 Marlowe Crest Ave, Philadelphia, PA 19139

Reception to follow after the symposium.

Also, please add - Register and upload abstracts for the symposium at www.qelvarn.example. Registration and abstract submission closes on January 4, 2018.

Keynote Speaker:
Greta Lindqvar, Ph.D.
NVOS Director General; Professor, Ostrel Academy; Director, Genetics and Developmental Biology at Institut Varanne
Ostrel Academy, NVOS, Institut Varanne
"Title of talk TBA."

Speakers:
Rina Fostwell, Ph.D.
Assistant Professor of Cell and Developmental Biology
Dunmore State University, TKHV
"Title of talk TBA."

Owen Trask, Ph.D.
Assistant Professor of Genetics
"Title of talk TBA."

Lia Vestur, Ph.D.
Professor, Grauwald University
Otto Ferlsang Center for Molecular Medicine
"Title of talk TBA."

Hao Lin, Ph.D.
Professor of Cellular and Molecular Medicine
Coastal Meridian University
"Title of talk TBA."

Jun Zhao, Ph.D.
Associate Professor of Pediatrics
The Riverbend Youth Medical Center
"Spatial genome re-organization between fetal and adult hematopoietic stem cells."

Mei Sun, Ph.D.
Professor, Department of Genetics
Pellridge Medical School
"Title of talk TBA."

```html
<!DOCTYPE html>
<html lang="en">
<head>
<meta charset="utf-8">
<title>Layered and Regional Proteomics Colloquium</title>
<link rel="stylesheet" href="https://fonts.googleapis.com/css2?family=Lato:wght@400;700;900&family=Merriweather:wght@700;900&display=swap">
<style>
:root{
  --backdrop:#1f2326;
  --maroon:#7a1023;
  --navy:#0f2a66;
  --navy-deep:#0b1f52;
  --ice:#b9d3f2;
  --card:#dee1e0;
  --ink:#1d1d1d;
  --white:#ffffff;
}
*{box-sizing:border-box;margin:0;padding:0}
html,body{width:1200px;height:1200px;overflow:hidden;background:var(--backdrop)}
.flyer{position:absolute;left:213px;top:53px;width:968px;height:1368px;background:var(--white);transform:scale(0.8);transform-origin:0 0;font-family:"Lato",sans-serif;color:var(--ink);overflow:hidden}
.backdrop-art{position:absolute;inset:0}
.brand{position:absolute;font-family:"Lato",sans-serif;font-weight:700;color:var(--navy);font-size:26px;line-height:1.05}
.brand-engineering{left:46px;top:40px;display:flex;align-items:center;gap:12px}
.brand-engineering .mark{width:42px;height:42px;background:var(--navy)}
.brand-institute{left:276px;top:48px;display:flex;align-items:center;gap:10px;font-size:20px}
.brand-institute .mark{width:40px;height:40px;border-radius:50%;background:var(--maroon)}
.event-title{position:absolute;right:46px;top:36px;text-align:right;font-family:"Merriweather",serif;font-weight:900;color:var(--maroon);font-size:25px;line-height:1.14;text-transform:uppercase}
.sponsor{position:absolute;right:46px;top:102px;text-align:right;font-family:"Merriweather",serif;font-weight:700;font-size:15px;line-height:1.3;color:var(--ink)}
.keynote{position:absolute;left:47px;top:232px;width:330px;color:var(--white)}
.keynote h2{font-weight:900;font-size:34px;color:var(--ice);letter-spacing:.3px;white-space:nowrap}
.keynote .name{font-size:19px;margin:12px 0 14px}
.keynote ul{list-style:none;font-size:14.5px;line-height:1.15;width:275px}
.keynote li{position:relative;padding-left:16px;margin-bottom:8px}
.keynote li::before{content:"";position:absolute;left:2px;top:5px;width:7px;height:7px;border-radius:50%;background:var(--white)}
.speakers-title{position:absolute;left:64px;top:556px;font-weight:900;font-size:31px;color:var(--maroon)}
.speaker{position:absolute;width:400px;height:160px}
.speaker .card{position:absolute;left:128px;top:16px;width:266px;height:133px;background:var(--card);border-radius:10px}
.speaker .photo{position:absolute;left:0;top:0;width:160px;height:160px;border-radius:50%;box-shadow:0 3px 8px rgba(0,0,0,.35)}
.speaker .bio{position:absolute;left:176px;top:0;width:216px;height:160px;display:flex;flex-direction:column;justify-content:center;font-size:14px;line-height:1.22}
.registration{position:absolute;left:0;right:0;top:1148px;text-align:center;font-size:19px;line-height:1.22}
.registration .link{font-weight:900;color:var(--navy)}
.registration .deadline{font-weight:900;color:var(--maroon)}
.event-date{position:absolute;left:44px;top:1266px;color:var(--white)}
.event-date .label{font-size:31px;line-height:1.1}
.event-date .day{font-weight:900;font-size:32px;line-height:1.2}
.divider{position:absolute;left:444px;top:1264px;width:3px;height:94px;background:var(--white)}
.venue{position:absolute;left:538px;top:1276px;width:400px;color:var(--white);font-size:19.5px;line-height:1.22}
</style>
</head>
<body>
<main class="flyer">
  <svg class="backdrop-art" width="968" height="1368" viewBox="0 0 968 1368" aria-hidden="true">
    <defs>
      <linearGradient id="helix-tone" x1="0" y1="0" x2="1" y2="1">
        <stop offset="0" stop-color="#3d6bb5"/>
        <stop offset=".5" stop-color="#7ea6db"/>
        <stop offset="1" stop-color="#c3d7ef"/>
      </linearGradient>
      <linearGradient id="portrait-tone" x1="0" y1="0" x2="0" y2="1">
        <stop offset="0" stop-color="#5a3322"/>
        <stop offset=".45" stop-color="#c99a82"/>
        <stop offset="1" stop-color="#eef0f2"/>
      </linearGradient>
    </defs>
    <rect x="0" y="118" width="968" height="520" fill="url(#helix-tone)"/>
    <rect x="32" y="118" width="350" height="394" fill="var(--navy-deep)"/>
    <path d="M0 0 H968 V135 C800 180 650 220 500 218 C300 215 150 170 0 125 Z" fill="var(--white)"/>
    <path d="M430 218 C650 214 820 168 968 134 V160 C820 196 650 224 500 224 Z" fill="var(--maroon)"/>
    <path d="M0 512 C300 518 620 560 968 628 V1368 H0 Z" fill="var(--white)"/>
    <path d="M0 514 C150 514 280 518 380 530 C250 530 120 532 0 536 Z" fill="var(--maroon)"/>
    <path d="M0 1214 C300 1226 700 1212 968 1196 V1368 H0 Z" fill="var(--navy)"/>
    <path d="M0 1226 C300 1238 700 1226 968 1210 V1368 H0 Z" fill="var(--maroon)"/>
  </svg>

  <svg style="position:absolute;left:670px;top:215px" width="298" height="420" viewBox="0 0 298 420" role="img" aria-label="Portrait photograph of keynote speaker Greta Lindqvar">
    <path d="M0 0 H298 V413 C200 392 100 378 0 368 Z" fill="url(#portrait-tone)"/>
  </svg>

  <div class="brand brand-engineering"><span class="mark"></span><span>Dorwick<br>Engineering</span></div>
  <div class="brand brand-institute"><span class="mark"></span><span>Dorwick Chromatin<br>Institute</span></div>

  <h1 class="event-title">Layered and Regional<br>Proteomics Colloquium</h1>
  <p class="sponsor">Sponsored by the Dorwick Chromatin Institute and<br>the Department of Bioengineering</p>

  <section class="keynote">
    <h2>KEYNOTE SPEAKER</h2>
    <p class="name">GRETA LINDQVAR,</p>
    <ul>
      <li>Ph.D. NVOS</li>
      <li>Director General;</li>
      <li>Professor, Ostrel Academy;</li>
      <li>Director, Genetics and Developmental Biology at Institut Varanne</li>
      <li>Ostrel Academy, NVOS, Institut Varanne</li>
      <li>"Title of talk TBA."</li>
    </ul>
  </section>

  <h2 class="speakers-title">SPEAKER</h2>

  <article class="speaker" style="left:42px;top:612px">
    <div class="card"></div>
    <div class="photo" role="img" aria-label="Portrait photograph of Rina Fostwell" style="background:radial-gradient(circle at 50% 40%,#c79a84,#5b3a2c 70%,#b24a3a)"></div>
    <div class="bio">Rina Fostwell, Ph.D.<br>Assistant Professor of Cell and Developmental Biology<br>Dunmore State University, TKHV<br>"Title of talk TBA."</div>
  </article>
  <article class="speaker" style="left:477px;top:612px">
    <div class="card"></div>
    <div class="photo" role="img" aria-label="Portrait photograph of Owen Trask" style="background:radial-gradient(circle at 50% 45%,#e2b49a,#8a4a3a 65%,#6e2a2a)"></div>
    <div class="bio">Owen Trask, Ph.D.<br>Assistant Professor of Genetics<br>Dunmore State University, TKHV<br>"Title of talk TBA."</div>
  </article>
  <article class="speaker" style="left:42px;top:792px">
    <div class="card"></div>
    <div class="photo" role="img" aria-label="Portrait photograph of Lia Vestur" style="background:radial-gradient(circle at 50% 50%,#d3aa94,#4a3a33 70%,#777)"></div>
    <div class="bio">Lia Vestur, Ph.D.<br>Professor, Grauwald University<br>Otto Ferlsang Center for Molecular Medicine<br>"Title of talk TBA."</div>
  </article>
  <article class="speaker" style="left:477px;top:792px">
    <div class="card"></div>
    <div class="photo" role="img" aria-label="Portrait photograph of Hao Lin" style="background:radial-gradient(circle at 50% 50%,#d9a47e,#8a5a3e 60%,#e8e8e8)"></div>
    <div class="bio">Hao Lin, Ph.D.<br>Professor of Cellular and Molecular Medicine<br>Coastal Meridian University<br>"Title of talk TBA."</div>
  </article>
  <article class="speaker" style="left:42px;top:975px">
    <div class="card" style="height:140px;top:10px"></div>
    <div class="photo" role="img" aria-label="Portrait photograph of Jun Zhao" style="background:radial-gradient(circle at 50% 45%,#e0b597,#6e4a3a 60%,#9bb7d8)"></div>
    <div class="bio">Jun Zhao, Ph.D.<br>Associate Professor of Pediatrics<br>The Riverbend Youth Medical Center<br>"Spatial genome re-organization between fetal and adult hematopoietic stem cells."</div>
  </article>
  <article class="speaker" style="left:477px;top:975px">
    <div class="card" style="height:140px;top:10px"></div>
    <div class="photo" role="img" aria-label="Portrait photograph of Mei Sun" style="background:radial-gradient(circle at 50% 50%,#d6ad92,#3a3a30 60%,#5e7a4a)"></div>
    <div class="bio">Mei Sun, Ph.D.<br>Professor, Department of Genetics<br>Pellridge Medical School<br>"Title of talk TBA."</div>
  </article>

  <p class="registration">Register and upload abstracts for the symposium at <span class="link">www.qelvarn.example.</span><br>Registration and abstract submission closes on <span class="deadline">January 4, 2018.</span></p>

  <div class="event-date">
    <p class="label">Date &amp; Time</p>
    <p class="day">JANUARY 8, 2018</p>
  </div>
  <div class="divider"></div>
  <p class="venue">Halvorsen Auditorium, Brantley Center for Applied Discovery, 2175 Marlowe Crest Ave, Philadelphia, PA 19139</p>
</main>
</body>
</html>
```